Need website for LED Signs company

Need an web page for a sign company. Basic home page / Tab for photo gallery (projects), tab for other projects could be photo gallery type with the ability for descriptions gallery to be able to have albums (projects) and tab for about us / testimonials Should be easy for me to change with dreamweaver or easy to change add remove content. I will provide pictures and content I would be happy if it could be set up like a template where i can add the content after but i would provide as much content as possible the current page is http://glowcrestsigns.ca examples of my competition:https://metroled.com/led-message-signs/http://www.libertevision.com/https://www.daktronics.com/en-us/products/message-displaysSEO optimized

1 page

• I want to feature LED signs and EMC's the Special projects tab tab will or should be a photo type gallery that is easy to add photos with detailed descriptions
• I do not want to wast peoples time making something similar to what i have now.
• To help me pick a winner Please show links to some of the sites you have created in the past. .

```html
<!DOCTYPE html>
<html lang="en">
<head>
<meta charset="utf-8">
<title>Glowcrest Signs – LED Signs &amp; Displays</title>
<link href="https://fonts.googleapis.com/css2?family=Lato:wght@400;700;900&display=swap" rel="stylesheet">
<style>
:root{
  --black:#000;
  --ink:#333;
  --blue:#1147d8;
  --red:#e0161e;
  --green:#3ddc3d;
  --card:#ececec;
  --footer:#2b2b2b;
  --white:#fff;
}
*{margin:0;padding:0;box-sizing:border-box}
html,body{width:1200px;height:3120px;overflow:hidden}
body{font-family:'Lato',sans-serif;color:var(--ink);background:var(--white);position:relative}

.site-header{position:absolute;top:0;left:0;width:1200px;height:108px;background:var(--black);display:flex;align-items:center;justify-content:space-between;padding:0 75px}
.brand{display:flex;align-items:center;gap:12px;color:var(--white);font-weight:900;font-size:36px;letter-spacing:-0.5px}
.brand-dot{width:14px;height:14px;border-radius:50%;background:var(--white)}
.main-nav{display:flex;gap:38px}
.main-nav a{color:var(--white);text-decoration:none;font-size:13px;font-weight:700}
.main-nav a.active{color:var(--green)}

.hero{position:absolute;top:108px;left:0;width:1200px;height:608px;background:radial-gradient(circle at 85% 50%,#1a6c72 0%,#0c2a30 30%,transparent 55%),linear-gradient(90deg,#2a1a18 0%,#3a2a26 30%,#1b1d22 60%,#0b1518 100%)}
.hero-title{position:absolute;left:75px;top:193px;color:var(--white);font-size:70px;font-weight:900;line-height:76px;text-shadow:0 2px 6px rgba(0,0,0,.5)}
.hero-dots{position:absolute;left:75px;top:540px;display:flex;gap:9px}
.hero-dots span{width:12px;height:12px;border-radius:50%;background:var(--white)}
.hero-dots span.on{background:var(--red)}

.welcome{position:absolute;top:716px;left:0;width:1200px;height:386px;text-align:center}
.welcome h1{margin-top:60px;color:var(--blue);font-size:54px;font-weight:900;line-height:58px}
.welcome p{margin:28px auto 0;width:880px;font-size:17px;line-height:31px;color:#333}

.band{position:absolute;left:0;width:1200px;height:360px;background:radial-gradient(circle at 80% 60%,#3a1670 0%,transparent 45%),linear-gradient(90deg,#0d1512,#1c2a24 40%,#111820 100%)}
.band h2{color:var(--white);text-align:center;font-size:54px;font-weight:900;padding-top:60px}
.services-band{top:1102px}
.contact-band{top:2338px;background:radial-gradient(circle at 70% 40%,#4a1a80 0%,transparent 45%),linear-gradient(90deg,#0b0b10,#1a1a24 50%,#130d1c 100%)}

.card{position:absolute;left:75px;width:1050px;background:var(--card)}
.services-card{top:1275px;height:379px}
.services-photo{position:absolute;left:37px;top:40px;width:475px;height:297px;background:linear-gradient(180deg,#b9c3cc 0%,#8f99a2 55%,#4d5a3a 100%)}
.services-text{position:absolute;left:539px;top:45px;width:460px;font-size:16px;line-height:31px;color:#333}
.services-text p+p{margin-top:12px}
.btn{display:inline-block;background:var(--red);color:var(--white);font-weight:700;font-size:16px;text-align:center;text-decoration:none}
.services-card .btn{position:absolute;left:539px;top:270px;width:151px;height:46px;line-height:46px}

.gallery-title{position:absolute;top:1700px;left:0;width:1200px;text-align:center;color:var(--blue);font-size:54px;font-weight:900}
.gallery-grid{position:absolute;top:1806px;left:75px;width:1050px;display:grid;grid-template-columns:repeat(3,339px);grid-auto-rows:224px;column-gap:17px;row-gap:17px}
.tile{display:block}
.t1{background:radial-gradient(circle,#3b6dff 0%,#0a1a8a 70%)}
.t2{background:linear-gradient(180deg,#c9ccd0,#6a7078)}
.t3{background:linear-gradient(135deg,#0a1420,#1f5a7a 60%,#3a1a1a)}
.t4{background:linear-gradient(90deg,#e8d22a 0 40%,#e6e6e6 40%)}
.t5{background:linear-gradient(90deg,#2a1a18,#1a5a60)}
.t6{background:linear-gradient(180deg,#0d1424,#2a2a30)}

.contact-card{top:2511px;height:376px}
.contact-line{position:absolute;top:30px;left:0;width:1050px;text-align:center;font-size:17px;display:flex;justify-content:center;align-items:center;gap:10px}
.contact-line svg{display:block}
.field{position:absolute;background:var(--white);font-size:14px;color:#666;padding:0 16px;line-height:46px}
.f-name{left:89px;top:91px;width:423px;height:46px}
.f-email{left:89px;top:147px;width:423px;height:46px}
.f-phone{left:89px;top:205px;width:423px;height:46px}
.f-message{left:539px;top:91px;width:422px;height:160px}
.contact-card .btn{position:absolute;left:449px;top:278px;width:152px;height:44px;line-height:44px}

.site-footer{position:absolute;top:2948px;left:0;width:1200px;height:172px;background:var(--footer);color:var(--white);text-align:center}
.footer-nav{display:flex;justify-content:center;gap:36px;padding-top:47px}
.footer-nav a{color:var(--white);text-decoration:none;font-size:13px;font-weight:700}
.copyright{margin-top:14px;font-size:12px}
.social{display:flex;justify-content:center;gap:16px;margin-top:16px}
.social span{width:22px;height:22px;border-radius:50%;background:var(--white)}
</style>
</head>
<body>

<header class="site-header">
  <div class="brand"><span>Glowcrest Signs</span><span class="brand-dot"></span></div>
  <nav class="main-nav">
    <a class="active" href="#">HOME</a>
    <a href="#">ABOUT US</a>
    <a href="#">SERVICES</a>
    <a href="#">GALLERY</a>
    <a href="#">OTHER PROJECTS</a>
    <a href="#">TESTIMONIALS</a>
    <a href="#">CONTACT US</a>
  </nav>
</header>

<section class="hero" role="img" aria-label="Night street with a glowing LED billboard of social media words">
  <h2 class="hero-title">THE FUTURE OF<br>L.E.D TECHNOLOGY</h2>
  <div class="hero-dots"><span class="on"></span><span></span><span></span><span></span></div>
</section>

<section class="welcome">
  <h1>WELCOME TO<br>GLOWCREST SIGNS</h1>
  <p>Glowcrest Signs is not your average L.E.D. Company. Our technology and custom made LED modules have what is takes to make your custom project come to life. Our team will work with you to create your wildest projects. No project is to big or to small. From digital signage, video walls, window signs or custom made DJ booths, Glowcrest Signs will exceed your expectations.</p>
</section>

<section class="band services-band" role="img" aria-label="Close-up of LED lamp modules glowing in green and purple">
  <h2>SERVICES</h2>
</section>
<div class="card services-card">
  <div class="services-photo" role="img" aria-label="Portable LED message trailer beside a city road"></div>
  <div class="services-text">
    <p>We are a custom build service. If you can dream it, we can build it. From outdoor displays in your back yard, to massive video walls for indoor and outdoor applications.</p>
    <p>Lorem ipsum dolor sit amet, consectetur adipiscing elitc rutrum metus sed odio mollis accumsan. Cras ac turpis in massa tempus accumsan vel et ante.</p>
  </div>
  <a class="btn" href="#">READ MORE</a>
</div>

<h2 class="gallery-title">GALLERY</h2>
<div class="gallery-grid">
  <div class="tile t1" role="img" aria-label="Blue LED panel close-up"></div>
  <div class="tile t2" role="img" aria-label="Illuminated exit and parking signs in a garage"></div>
  <div class="tile t3" role="img" aria-label="Neon word sign about food and beverage"></div>
  <div class="tile t4" role="img" aria-label="Yellow LED screen in a shopping mall"></div>
  <div class="tile t5" role="img" aria-label="LED billboard of social media words at night"></div>
  <div class="tile t6" role="img" aria-label="Roadside billboards along a street at night"></div>
</div>

<section class="band contact-band" role="img" aria-label="Purple LED dot matrix background">
  <h2>CONTACT US</h2>
</section>
<div class="card contact-card">
  <div class="contact-line">
    <svg width="14" height="18" viewBox="0 0 14 18"><path d="M7 0C3 0 0 3 0 7c0 5 7 11 7 11s7-6 7-11c0-4-3-7-7-7z" fill="#e0161e"/><circle cx="7" cy="7" r="2.5" fill="#ececec"/></svg>
    <span>Brookvale, Saskatchewan S7T 4K2 Canada</span>
    <svg width="18" height="18" viewBox="0 0 24 24" style="margin-left:14px"><path d="M6.6 10.8a15 15 0 0 0 6.6 6.6l2.2-2.2a1 1 0 0 1 1-.25 11.4 11.4 0 0 0 3.6.57 1 1 0 0 1 1 1V20a1 1 0 0 1-1 1A17 17 0 0 1 3 4a1 1 0 0 1 1-1h3.5a1 1 0 0 1 1 1c0 1.25.2 2.45.57 3.6a1 1 0 0 1-.25 1z" fill="#e0161e"/></svg>
    <span>(306) 555-0148</span>
  </div>
  <div class="field f-name">Name</div>
  <div class="field f-email">Email Address</div>
  <div class="field f-phone">Phone No</div>
  <div class="field f-message">Message</div>
  <a class="btn" href="#">SUBMIT</a>
</div>

<footer class="site-footer">
  <nav class="footer-nav">
    <a href="#">HOME</a><a href="#">ABOUT US</a><a href="#">SERVICES</a><a href="#">GALLERY</a><a href="#">OTHER PROJECTS</a><a href="#">TESTIMONIALS</a><a href="#">CONTACT US</a>
  </nav>
  <p class="copyright">Copyright © 2019, Company Name. All Right reserved</p>
  <div class="social"><span></span><span></span><span></span><span></span><span></span></div>
</footer>

</body>
</html>
```